Simple, 1-Page Project - Life-saving AED Devices

We recently kicked off a project to bring all geographic location records for automatic emergency defibrillators (AEDs) in the State of New York online (instead of kept in paper in drawers). This hope is that is will ultimately save thousands of lives, as 9-1-1 operators will be able to quickly direct civilians to the nearest AED to bring to people suffering a cardiac event (e.g., a heart attack).

This page will be used to describe this effort, our progress thus far and how far we have left to go.

I am looking for a 1-page design - coded for both a responsive version for mobile devices and a traditional version - that would ***ideally*** plug into my existing WordPress site (https://qv-lmt.org), but it's not a requirement.

Target Market(s)

General public (non-physicians/non-EMTs)

Requirements
Must have
• - Our logo (please note, our logo is the Birchfield Vale Chapter logo...attached)
Nice to have
• - Would be wonderful to have an area with a clickable map showing where the participating regions are - which, once clicked, will take to you their specific sites. Regions are large chunks of land encompassing multiple towns, NOT a singular, specific place A nice-looking Google Map, a la Plumtail Grids (https://plumtailgrids.com/) would be cool if this were possible..
• - If you need a headline or page title, you can use: "Bringing AEDs in New York Online"
• - Would be nice if the design incorporated the color scheme of our brand (see attachment) and/or our main website: https://qv-lmt.org/
• - Would be nice to have some AED imagery - I attached some common symbols seen in AED advertising for inspiration
Should not have
• - This is a serious topic, so the design should be respectful and not too silly/cartoonish
• - Stock images, if chosen, should be thoughtful and classy

```html
<!DOCTYPE html>
<html lang="en">
<head>
<meta charset="utf-8">
<title>Bringing AEDs in New York – Mobile</title>
<link rel="stylesheet" href="https://fonts.googleapis.com/css2?family=Crimson+Text:ital,wght@0,400;1,700&family=Open+Sans:wght@400&display=swap">
<style>
  :root {
    --navy: #1c416b;
    --navy-deep: #1b3c63;
    --hero-top: #4a5666;
    --hero-bottom: #1e2632;
    --gold: #aba679;
    --bar: #3b4049;
    --map: #e6e7e9;
    --footer: #333333;
    --white: #ffffff;
    --dim: rgba(10, 16, 26, 0.72);
  }
  * { box-sizing: border-box; margin: 0; padding: 0; }
  html, body { width: 840px; height: 1200px; overflow: hidden; background: var(--white); }
  body { position: relative; font-family: "Open Sans", Arial, sans-serif; color: var(--white); }

  .screen { position: absolute; top: 56px; width: 224px; overflow: hidden; }
  .screen--page { left: 165px; height: 1054px; }
  .screen--menu { left: 428px; height: 404px; }

  .page { width: 224px; position: relative; }

  .site-header { height: 42px; background: var(--navy-deep); position: relative; }
  .brand { position: absolute; left: 11px; top: 7px; display: flex; align-items: center; gap: 6px; }
  .brand__mark { width: 26px; height: 26px; border-radius: 50%; border: 1.2px solid var(--white); }
  .brand__name { font-family: "Crimson Text", Georgia, serif; font-size: 9.5px; line-height: 10px; border-left: 1px solid var(--white); padding-left: 5px; }
  .brand__name small { display: block; font-size: 4.5px; letter-spacing: .4px; text-transform: uppercase; margin-top: 1px; }
  .menu-toggle { position: absolute; left: 192px; top: 15px; }

  .copy { font-size: 8.3px; line-height: 10.5px; text-align: center; }
  .title { font-family: "Crimson Text", Georgia, serif; font-style: italic; font-weight: 700; font-size: 17.5px; line-height: 21.5px; text-align: center; }

  .hero { height: 217px; position: relative; }
  .hero__photo { position: absolute; inset: 0; background: linear-gradient(180deg, var(--hero-top) 0%, #35404f 45%, var(--hero-bottom) 100%); }
  .hero__content { position: absolute; inset: 0; padding: 28px 12px 0; }
  .hero__icon { display: block; margin: 0 auto 10px; }
  .hero .copy { margin-top: 10px; }

  .about { height: 212px; background: var(--navy); padding: 18px 12px 0; }
  .about .copy { margin-top: 6px; }
  .button { display: block; width: 96px; height: 29px; margin: 17px auto 0; background: var(--gold); font-size: 9px; line-height: 29px; text-align: center; }

  .aed { height: 214px; position: relative; }
  .aed__photo { position: absolute; inset: 0; background: linear-gradient(180deg, #2b3646 0%, #3a4454 50%, #4d5561 100%); }
  .aed__content { position: absolute; inset: 0; padding: 37px 14px 0; }
  .aed__badge { width: 23px; height: 33px; margin: 0 auto; background: var(--white); border: 1px solid #444; }
  .aed .title { margin-top: 14px; }
  .aed .copy { margin-top: 7px; }

  .map-bar { height: 23px; background: var(--bar); font-size: 8.7px; line-height: 23px; text-align: center; }
  .map { height: 212px; background: linear-gradient(135deg, #eceef0 0%, var(--map) 55%, #dedfe2 100%); }

  .contact { height: 134px; background: var(--footer); padding: 22px 10px 0; font-size: 8.7px; line-height: 10.5px; text-align: center; }
  .contact p + p { margin-top: 10.5px; }

  .menu-backdrop { position: absolute; inset: 0; background: var(--dim); }
  .menu-panel { position: absolute; left: 72px; top: 0; width: 152px; height: 404px; background: var(--navy-deep); }
  .menu-list { list-style: none; margin: 0 auto; width: 77px; padding-top: 26px; }
  .menu-list li { font-size: 15px; line-height: 52px; text-align: center; border-bottom: 0.6px solid rgba(255,255,255,.35); }
  .menu-list li:first-child { line-height: 24px; padding-bottom: 14px; }
  .menu-list li:last-child { border-bottom: none; }
  .menu-close { position: absolute; left: 68px; top: 354px; }
</style>
</head>
<body>

<div class="screen screen--page">
  <div class="page">
    <header class="site-header">
      <div class="brand">
        <div class="brand__mark"></div>
        <div class="brand__name">Birchfield Vale<small>Chapter</small></div>
      </div>
      <svg class="menu-toggle" width="13" height="10" viewBox="0 0 13 10"><g stroke="#fff" stroke-width="1"><line x1="0" y1="1" x2="13" y2="1"/><line x1="0" y1="5" x2="13" y2="5"/><line x1="0" y1="9" x2="13" y2="9"/></g></svg>
    </header>

    <section class="hero">
      <div class="hero__photo" role="img" aria-label="Black-and-white aerial photo of the Manhattan skyline with a blue tint"></div>
      <div class="hero__content">
        <svg class="hero__icon" width="38" height="24" viewBox="0 0 38 24"><path d="M8 24a7 7 0 0 1-1-13.9A11 11 0 0 1 28 7.5 8.3 8.3 0 0 1 30 24Z" fill="#fff"/><path d="M19 19V7M14.5 11.5 19 7l4.5 4.5" stroke="#1e2632" stroke-width="1.8" fill="none"/></svg>
        <h1 class="title">Bringing AEDs<br>in New York</h1>
        <p class="copy">Our mission is to bring all geographic location records for Automatic External Defibrillators (AEDs) in the State of New York online and make them accessible to anyone in need. Currently, the survival rate of an out-of-hospital cardiac arrest is under 12%. We hope to help increase this rate by providing some much-needed information.</p>
      </div>
    </section>

    <section class="about">
      <h2 class="title">Who Are We?</h2>
      <p class="copy">The Birchfield Vale Chapter of the Meridian College of Cardiology (BVMCC) was founded in 1990, but our history in New York is much older. In fact the Meridian College of Cardiology (MCC) was started by a group of physicians from New York. The Chapter was formed for the purpose of contributing to the prevention of cardiovascular diseases and ensuring optimal quality of care for individuals with such diseases.</p>
      <a class="button">Find out more!</a>
    </section>

    <section class="aed">
      <div class="aed__photo" role="img" aria-label="Photo of a paramedic using a defibrillator on a patient beside an ambulance"></div>
      <div class="aed__content">
        <div class="aed__badge"></div>
        <h2 class="title">What is an AED?</h2>
        <p class="copy">An Automatic External Defibrillator is a portable electronic device that automatically diagnoses the life-threatening cardiac arrhythmias, and is able to treat them through the application of electricity which allows the heart to re-establish an effective rhythm.</p>
      </div>
    </section>

    <div class="map-bar">Automatic External Defibrillators in New York</div>
    <div class="map" role="img" aria-label="Light grey street map of Manhattan and surroundings with blue AED location pins"></div>

    <footer class="contact">
      <p>CONTACT<br>The Birchfield Vale Chapter of the<br>Meridian College of Cardiology</p>
      <p>214 Larkspur Avenue, Suite 610<br>New York, NY 10027</p>
      <p>(555) 014-2287<br>ask@qv-lmt.org</p>
    </footer>
  </div>
</div>

<div class="screen screen--menu">
  <div class="page" aria-hidden="true">
    <header class="site-header">
      <div class="brand">
        <div class="brand__mark"></div>
        <div class="brand__name">Birchfield Vale<small>Chapter</small></div>
      </div>
    </header>
    <section class="hero">
      <div class="hero__photo"></div>
      <div class="hero__content">
        <svg class="hero__icon" width="38" height="24" viewBox="0 0 38 24"></svg>
        <div class="title">Bringing AEDs<br>in New York</div>
        <p class="copy">Our mission is to bring all geographic location records for Automatic External Defibrillators (AEDs) in the State of New York online and make them accessible to anyone in need. Currently, the survival rate of an out-of-hospital cardiac arrest is under 12%. We hope to help increase this rate by providing some much-needed information.</p>
      </div>
    </section>
    <section class="about">
      <div class="title">Who Are We?</div>
      <p class="copy">The Birchfield Vale Chapter of the Meridian College of Cardiology (BVMCC) was founded in 1990, but our history in New York is much older. In fact the Meridian College of Cardiology (MCC) was started by a group of physicians from New York. The Chapter was formed for the purpose of contributing to the prevention of cardiovascular diseases and ensuring optimal quality of care for individuals with such diseases.</p>
    </section>
  </div>
  <div class="menu-backdrop"></div>
  <nav class="menu-panel">
    <ul class="menu-list">
      <li>About Us</li>
      <li>AEDs</li>
      <li>Map</li>
    </ul>
    <svg class="menu-close" width="16" height="16" viewBox="0 0 16 16"><g stroke="#fff" stroke-width="1.2"><line x1="1" y1="1" x2="15" y2="15"/><line x1="15" y1="1" x2="1" y2="15"/></g></svg>
  </nav>
</div>

</body>
</html>
```